Larkmoor Drones Business Card

We are a new company based in Central Queensland, Australia that uses specalised drones (Voskel Ferra Q80) to undertake mainly agricultural operations, like spraying weeds, spraying crops, spreading seed etc. I have attached a Plimbo proof of a card I was thinking along the lines of - purely a start point. The drone used in the business card MUST be a Voskel Ferra Q80.
I am very open to other ideas, especially fonts and layout. I don't have website etc set up yet.
The images are stock and easily interchangeable, I just ask that any background images reflect the local central Queensland area. The photo of the drone is not even complete (propellers cut off) and I need a new stock photo – I’m not sure if this is an issue, or I can pay for an image if need be. PLEASE FIND AN FERRA Q80 image - 4 sprayers, not 6.
The logo/business name is very draft and looking for further ideas, ideally incorporating drones or agriculture design elements into the design of the business name. The business name needs work on the graphic/design – it is a draft that I have included, the drone propellers (being a different colour) are DRAFT only and intended for changes. PLEASE DO NOT USE THE DRONE PORPELLER I HAVE USED AS A DRAFT. TRY TO FIND SOMETHING ELSE.. The arrow is a shape and not aligned in any way, I would also like ideas on different fonts and additional elements, like air streams, aviation elements, aviation or country western (farming like) themes and fonts etc.
Ideally looking at staying within the blue, green and yellow colours, keeping with an natural, outdoorsy, environmental feel.

Target Market(s)

Farmers, Agriculture, Local Governments, Land Managers

Industry/Entity Type

Agriculture, Drones, Aviation

Contact Information for Business Card

Agricultural Drone (Voskel Ferra Q80), Farming, Business Name.

Font styles to use
Sans Serif

Colors
0054AA
0677BA
7BADD7
CADEEF
E8F1F8
0094D4
00A9DD
6FCCEA
C7EBF8
E9F6FB
00AB8E
00BBA5
67D7C9
C6EFE9
E9F9F6
59FF00
82FF00
B8FF75
E3FFCB
F4FFEA

Requirements
Must have
• Voskel Ferra Q80 Drone
Should not have
• Tractors

```html
<!DOCTYPE html>
<html lang="en">
<head>
<meta charset="utf-8">
<title>Larkmoor Drones Business Card</title>
<link href="https://fonts.googleapis.com/css2?family=Russo+One&family=Montserrat:wght@500&family=Saira:wght@400&display=swap" rel="stylesheet">
<style>
  :root {
    --page: #1c1c1c;
    --navy: #1d3c8f;
    --white: #ffffff;
    --ink: #1f2430;
    --icon: #1d3c8f;
    --social: #0677ba;
  }
  * { margin: 0; padding: 0; box-sizing: border-box; }
  html, body { width: 1200px; height: 1059px; overflow: hidden; background: var(--page); }
  .card {
    position: absolute; left: 258px; width: 690px; height: 394px;
    border-radius: 30px; overflow: hidden;
  }
  .card--front { top: 91px; }
  .card--back { top: 548px; }
  .photo { position: absolute; inset: 0; }
  .photo--drone-field {
    background: linear-gradient(180deg, #5d8cc8 0%, #8fb6de 38%, #a9c3d8 52%, #6f8a78 60%, #4f7a3a 70%, #5b6068 73%, #6a6e76 100%);
  }
  .photo--drone-field::after {
    content: ""; position: absolute; left: 0; right: 0; top: 0; height: 100%;
    background: radial-gradient(ellipse 36% 42% at 50% 52%, rgba(40,42,48,.55), rgba(40,42,48,0) 70%);
  }
  .photo--sunset-field {
    background: linear-gradient(180deg, #c99a4a 0%, #f2c35a 18%, #f6dc9a 34%, #8aa07a 42%, #3f6a28 46%, #8c9a2a 58%, #6f8a22 75%, #3d5a14 100%);
  }
  .brand { position: absolute; left: 0; right: 0; text-align: center; }
  .brand__name { font-family: "Russo One", sans-serif; text-transform: uppercase; line-height: 1; }
  .brand__tagline { font-family: "Montserrat", sans-serif; font-weight: 500; text-transform: uppercase; letter-spacing: 0.12em; line-height: 1; }
  .card--front .brand { top: 28px; }
  .card--front .brand__name { font-size: 40px; color: var(--navy); }
  .card--front .brand__tagline { font-size: 13px; color: var(--ink); margin-top: 8px; }
  .card--back .brand { top: 262px; }
  .card--back .brand__name { font-size: 48px; color: var(--white); }
  .card--back .brand__tagline { font-size: 17px; color: var(--white); margin-top: 10px; }
  .contact { position: absolute; font-family: "Saira", sans-serif; color: var(--white); font-size: 17px; }
  .contact__row { display: flex; align-items: center; gap: 7px; height: 27px; }
  .contact__icon { width: 20px; height: 20px; flex: none; }
  .contact--direct { left: 34px; top: 290px; }
  .contact--social { left: 478px; top: 288px; }
  .contact--social .contact__row { height: 37px; gap: 12px; }
  .social-dot { width: 20px; height: 20px; border-radius: 50%; background: var(--social); flex: none; }
  .licence {
    position: absolute; left: 0; right: 0; top: 355px; text-align: center;
    font-family: "Saira", sans-serif; font-size: 11px; line-height: 13px; color: var(--white);
  }
  .services {
    position: absolute; left: 43px; right: 40px; top: 48px;
    display: flex; justify-content: space-between; align-items: center;
    font-family: "Russo One", sans-serif; font-size: 38px; color: var(--navy);
  }
  .services__dot { font-size: 24px; }
</style>
</head>
<body>
  <section class="card card--front">
    <div class="photo photo--drone-field" role="img" aria-label="Voskel Ferra Q80 agricultural spray drone on tarmac in front of a crop field and hills under blue sky"></div>
    <div class="brand">
      <p class="brand__name">Larkmoor Drones</p>
      <p class="brand__tagline">Servicing Central Queensland</p>
    </div>
    <div class="contact contact--direct">
      <div class="contact__row">
        <svg class="contact__icon" viewBox="0 0 20 20"><circle cx="10" cy="10" r="10" fill="var(--icon)"/><path d="M7 5.5l1.8 2.4-1 1.2c.7 1.4 1.8 2.4 3.1 3.1l1.2-1 2.4 1.8-.9 1.6c-3.9-.4-7.4-3.9-7.8-7.8z" fill="#fff"/></svg>
        <span>07 4921 3058</span>
      </div>
      <div class="contact__row">
        <svg class="contact__icon" viewBox="0 0 20 20"><circle cx="10" cy="10" r="10" fill="var(--icon)"/><rect x="5" y="6.5" width="10" height="7" fill="#fff"/><path d="M5 6.8l5 3.7 5-3.7" fill="none" stroke="var(--icon)" stroke-width="1.2"/></svg>
        <span>larkmoordrone@fieldpost.net</span>
      </div>
      <div class="contact__row">
        <svg class="contact__icon" viewBox="0 0 20 20"><circle cx="10" cy="10" r="10" fill="var(--icon)"/><circle cx="10" cy="10" r="5.5" fill="none" stroke="#fff" stroke-width="1.3"/><path d="M4.5 10h11M10 4.5c-2.4 3-2.4 8 0 11M10 4.5c2.4 3 2.4 8 0 11" fill="none" stroke="#fff" stroke-width="1"/></svg>
        <span>www.larkmoordrones.au</span>
      </div>
    </div>
    <div class="contact contact--social">
      <div class="contact__row"><span class="social-dot"></span><span>@larkmoordrone</span></div>
      <div class="contact__row"><span class="social-dot"></span><span>@larkmoordrone</span></div>
    </div>
    <p class="licence">Fully Licensed an insured<br>RePL 3571906; ReOC 4820; PCR B718263</p>
  </section>

  <section class="card card--back">
    <div class="photo photo--sunset-field" role="img" aria-label="Golden sunset sky over a green crop field with distant Central Queensland hills"></div>
    <div class="services">
      <span>SPRAY</span><span class="services__dot">•</span>
      <span>WEED</span><span class="services__dot">•</span>
      <span>SEED</span><span class="services__dot">•</span>
      <span>FEED</span>
    </div>
    <div class="brand">
      <p class="brand__name">Larkmoor Drones</p>
      <p class="brand__tagline">Servicing Central Queensland</p>
    </div>
  </section>
</body>
</html>
```